Distribution/Printing company needs a web site to inform prospective customers on what we do.

Distribution/Printing/Packaging company needs a web site to inform prospective customers on what we do. Please look at our direct to consumer web site (under development) for an idea of the product lines we sell: storedev.maplewickhaven.com
Logo files are attached as is a flyer that is under development which contains other information about the company (this is to be used for content- not to be posted as is). The web site should be focused on our business customer base and is not intended to be direct to consumer. Site should have a link to our consumer web site.
Site design should be mobile friendly, or mobile could be redirected to a mobile version. This web site will be strictly informational and will not be designed for any sales transactions.

Target Market(s)

Manufacturing and retail businesses, any other multi-site business that would benefit from centralized pricing and budget controls we can provide (banks, medical/dental offices, educational facilities, etc).

Industry/Entity Type

It Company

Coding

Coded - Design and coding required

Number of Pages Required

5+ page

Requirements
Must have
• 1) Top level menu: Products, about us, locations, contact us, news
• 2) page with news/promotions that is easily updated
• 3) "contact us" form (name, company, phone, email address) email link
• 4) link to www.store.maplewickhaven.com with information that lower pricing is available for businesses
• 5) SEO keywords
• 6) Link to powerpoint presentation file
Nice to have
• 1) our phone number should appear on every page near the top

```html
<!DOCTYPE html>
<html lang="en">
<head>
<meta charset="utf-8">
<title>Maplewick Haven Supply — Packaging, Printing, Distribution</title>
<link rel="stylesheet" href="https://fonts.googleapis.com/css2?family=Roboto+Condensed:wght@400;700&family=Open+Sans:wght@400;600&family=Arimo:wght@400;700&display=swap">
<style>
:root{
  --white:#ffffff;
  --ink:#1b1b1b;
  --navy:#1a6a9c;
  --nav-top:#3a93c2;
  --nav-bottom:#17628f;
  --sky:#2f9ad0;
  --sky-light:#6cc2ea;
  --sky-deep:#1a7fb8;
  --panel-dark:#1d1d1d;
  --field:#3a3a3a;
  --accent:#3aa6de;
  --footer-text:#e8f5fc;
  --bar:#1a1a1a;
}
*{box-sizing:border-box;margin:0;padding:0}
html,body{width:1029px;height:1200px;overflow:hidden}
body{font-family:"Arimo",Arial,sans-serif;color:var(--ink);background:var(--sky)}
.page{position:relative;width:1029px;height:1200px;overflow:hidden;
  background:radial-gradient(ellipse at 50% 35%,var(--sky-light) 0%,var(--sky) 45%,var(--sky-deep) 100%)}
.abs{position:absolute}

/* header */
.site-header{position:absolute;left:0;top:0;width:1029px;height:120px;background:var(--white)}
.brand{left:91px;top:30px}
.brand-name{font-family:"Roboto Condensed",sans-serif;font-weight:700;font-size:19px;letter-spacing:.3px;color:var(--ink);display:flex;align-items:center;gap:8px}
.brand-mark{width:12px;height:12px;background:var(--ink)}
.brand-tagline{font-family:"Roboto Condensed",sans-serif;font-size:13px;color:var(--ink);margin-top:10px;margin-left:20px}
.language{left:812px;top:8px;width:131px;height:19px;background:linear-gradient(#f4f4f4,#dcdcdc);border:1px solid #c9c9c9;border-radius:2px;font-size:11px;line-height:17px;padding-left:14px;color:#222}
.language::after{content:"";position:absolute;right:0;top:-1px;width:22px;height:19px;background:#2a2a2a}
.language svg{position:absolute;right:6px;top:5px;z-index:1}
.main-nav{left:437px;top:46px;width:506px;height:50px;border-radius:5px;
  background:linear-gradient(var(--nav-top),var(--nav-bottom));box-shadow:0 4px 6px rgba(0,0,0,.25);display:flex}
.main-nav a{color:var(--white);text-decoration:none;font-family:"Arimo",sans-serif;font-size:16px;line-height:50px;text-align:center;border-right:1px solid rgba(0,0,0,.25)}
.main-nav a:last-child{border-right:none}

/* hero (children positioned inside the hero box) */
.hero{left:0;top:120px;width:1029px;height:281px}
.hero-photo{left:429px;top:0;width:440px;height:281px;
  background:linear-gradient(100deg,rgba(40,60,80,0) 0%,#2b3440 35%,#1b2028 70%,rgba(30,80,120,.2) 100%)}
.hero-title{left:88px;top:38px;font-family:"Roboto Condensed",sans-serif;font-weight:700;font-size:41px;color:var(--white);line-height:1;white-space:nowrap}
.hero-sub{left:89px;top:70px;font-family:"Open Sans",sans-serif;font-size:25px;line-height:1.2;color:var(--ink);white-space:nowrap}
.hero-with{left:92px;top:104px;font-family:"Roboto Condensed",sans-serif;font-weight:700;font-size:56px;line-height:1.1;color:#e6e6e6;text-shadow:0 2px 0 #9a9a9a,0 4px 6px rgba(0,0,0,.3);white-space:nowrap}
.slider-dots{left:103px;top:245px;display:flex;gap:7px}
.slider-dots span{width:12px;height:12px;border-radius:50%;background:#dfeef6;border:2px solid #8fb7cc}
.slider-dots span.active{background:#1f5f86}

/* services panel */
.content-panel{left:86px;top:401px;width:857px;height:563px;background:var(--white);border-radius:6px}
.service{position:absolute;top:416px;width:260px;text-align:center}
.service-photo{width:190px;height:190px;margin:0 auto;border-radius:50%;border:7px solid #e3e3e3;box-shadow:0 2px 4px rgba(0,0,0,.2)}
.photo-packaging{background:linear-gradient(135deg,#d8333f 0%,#c0403d 40%,#b38a61 60%,#8b6a4a 100%)}
.photo-printing{background:linear-gradient(135deg,#f2e21b 0%,#e5c616 30%,#d8289a 55%,#2aa4d8 80%,#3a3a3a 100%)}
.photo-distribution{background:linear-gradient(180deg,#c7c0b0 0%,#a78b63 50%,#8b7558 100%)}
.service-title{font-family:"Roboto Condensed",sans-serif;font-weight:700;font-size:22px;color:var(--navy);margin-top:15px}
.service-text{font-size:11px;line-height:16.5px;color:var(--ink);margin:6px auto 0;width:236px}
.more-button{display:block;width:76px;height:37px;margin:14px auto 0;border-radius:5px;
  background:linear-gradient(#3d97c6,#145f8d);box-shadow:0 2px 3px rgba(0,0,0,.35);
  color:var(--white);font-family:"Roboto Condensed",sans-serif;font-weight:700;font-size:19px;line-height:37px;text-decoration:none}

/* message form */
.message-box{left:123px;top:806px;width:782px;height:135px;background:var(--panel-dark);border-radius:3px}
.envelope{left:117px;top:789px;width:72px;height:63px;background:linear-gradient(135deg,#f7f7f7,#d9d9d9);transform:rotate(-14deg);border:2px solid #c8c8c8}
.message-heading{left:123px;top:817px;width:782px;padding-left:110px;font-family:"Arimo",sans-serif;font-weight:700;font-size:18px;color:var(--accent);text-align:center;white-space:nowrap}
.field{background:var(--field);border:1px solid #555;border-radius:3px;color:#9a9a9a;font-size:12px;padding:11px 13px}
.field-message{left:153px;top:851px;width:544px;height:71px}
.field-email{left:715px;top:850px;width:163px;height:28px;padding:6px 13px}
.send-button{left:715px;top:884px;width:163px;height:39px;border-radius:3px;background:linear-gradient(#ffffff,#cfcfcf);
  font-family:"Roboto Condensed",sans-serif;font-weight:700;font-size:20px;color:#2a2a2a;text-align:center;line-height:39px}

/* footer */
.footer-heading{font-family:"Roboto Condensed",sans-serif;font-weight:700;font-size:21px;color:var(--white);top:989px}
.footer-divider{top:983px;width:1px;height:149px;background:rgba(255,255,255,.35)}
.contact-row{left:95px;font-size:12.5px;color:var(--footer-text);display:flex}
.contact-row dt{width:75px;font-weight:700}
.contact-row dd{width:160px;line-height:14px}
.social-link{left:380px;width:141px;height:24px;background:var(--white);border:1px solid #c9c9c9;border-radius:2px;
  font-size:11px;color:#222;display:flex;align-items:center;padding-left:5px;gap:5px;white-space:nowrap;text-decoration:none}
.social-link i{width:12px;height:12px;background:#6f6f6f;flex:none}
.social-link b{font-weight:700}
.blog-item{left:573px;font-size:12.5px;color:var(--footer-text);display:flex;align-items:center;gap:8px}
.partner-badge{width:65px;height:46px;background:var(--white);border-radius:3px;box-shadow:0 1px 2px rgba(0,0,0,.25)}
.bottom-bar{left:0;top:1157px;width:1029px;height:43px;background:var(--bar);color:var(--white);font-size:10.5px;text-align:center;line-height:43px}
</style>
</head>
<body>
<div class="page">

  <header class="site-header">
    <div class="abs brand">
      <div class="brand-name"><span class="brand-mark"></span>MAPLEWICK HAVEN SUPPLY</div>
      <div class="brand-tagline">Packaging • Printing • Distribution</div>
    </div>
    <div class="abs language">Select Language
      <svg width="9" height="7" viewBox="0 0 9 7"><path d="M0 0h9L4.5 7z" fill="#fff"/></svg>
    </div>
    <nav class="abs main-nav">
      <a href="#" style="width:80px">Home</a>
      <a href="#" style="width:111px">About Us</a>
      <a href="#" style="width:82px">Offer</a>
      <a href="#" style="width:123px">Experience</a>
      <a href="#" style="width:110px">Contact</a>
    </nav>
  </header>

  <section class="abs hero" aria-label="Featured">
    <div class="abs hero-photo" role="img" aria-label="Businessman in a dark suit drawing a rising arrow"></div>
    <h1 class="abs hero-title">MAKE YOUR COMPANY</h1>
    <p class="abs hero-sub">a world wide known name</p>
    <p class="abs hero-with">WITH US</p>
    <div class="abs slider-dots"><span></span><span class="active"></span><span></span></div>
  </section>

  <main>
    <div class="abs content-panel"></div>

    <article class="service" style="left:99px">
      <div class="service-photo photo-packaging" role="img" aria-label="Red and brown packaging boxes"></div>
      <h2 class="service-title">PACKAGING</h2>
      <p class="service-text">Lorem ipsum dolor sit amet, consectetuer adipiscing elit, sed diam nonummy nibh euismod tincidunt ut laoreet dolore magna aliqu lorem Ipsum dolor sit am erat volutpa.</p>
      <a class="more-button" href="#">more</a>
    </article>

    <article class="service" style="left:387px">
      <div class="service-photo photo-printing" role="img" aria-label="Coloured printing press rollers"></div>
      <h2 class="service-title">PRINTING</h2>
      <p class="service-text">Lorem ipsum dolor sit amet, consectetuer adipiscing elit, sed diam nonummy nibh euismod tincidunt ut laoreet dolore magna aliqu lorem Ipsum dolor sit am erat volutpa.</p>
      <a class="more-button" href="#">more</a>
    </article>

    <article class="service" style="left:663px">
      <div class="service-photo photo-distribution" role="img" aria-label="Warehouse full of stacked boxes"></div>
      <h2 class="service-title">DISTRIBUTION</h2>
      <p class="service-text">Lorem ipsum dolor sit amet, consectetuer adipiscing elit, sed diam nonummy nibh euismod tincidunt ut laoreet dolore magna aliqu lorem Ipsum dolor sit am erat volutpa.</p>
      <a class="more-button" href="#">more</a>
    </article>

    <section class="abs message-box" aria-label="Message form"></section>
    <div class="abs envelope" role="img" aria-label="Airmail envelope"></div>
    <h3 class="abs message-heading">Write your message and give details about your company and activities.</h3>
    <div class="abs field field-message">Your message</div>
    <div class="abs field field-email">Email</div>
    <div class="abs send-button">send</div>
  </main>

  <footer>
    <h4 class="abs footer-heading" style="left:95px">Contact</h4>
    <dl>
      <div class="abs contact-row" style="top:1031px"><dt>Tel :</dt><dd>123.123.1234, 456.456.4567</dd></div>
      <div class="abs contact-row" style="top:1056px"><dt>Email :</dt><dd>info@maplewickhaven.com</dd></div>
      <div class="abs contact-row" style="top:1080px"><dt>Address :</dt><dd style="font-size:11px">13/4, Lorem ipsum dolor sit amet, consectetuer adipiscing ON, xyz</dd></div>
    </dl>
    <div class="abs footer-divider" style="left:354px"></div>

    <h4 class="abs footer-heading" style="left:380px">Social Media</h4>
    <a class="abs social-link" href="#" style="top:1030px"><i></i><span>Follow us on <b>Chirpline</b></span></a>
    <a class="abs social-link" href="#" style="top:1057px"><i></i><span>Find us on <b>Friendbook</b></span></a>
    <a class="abs social-link" href="#" style="top:1083px"><i></i><span>Join us on <b>Circlenet</b></span></a>
    <a class="abs social-link" href="#" style="top:1110px"><i></i><span>Watch us on <b>ClipStream</b></span></a>
    <div class="abs footer-divider" style="left:546px"></div>

    <h4 class="abs footer-heading" style="left:570px">Blog</h4>
    <div class="abs blog-item" style="top:1031px"><svg width="9" height="11" viewBox="0 0 9 11"><path d="M0 0h6l3 3v8H0z" fill="#dff1fb"/></svg>Lorem ipsum dolor sit amet.</div>
    <div class="abs blog-item" style="top:1057px"><svg width="9" height="11" viewBox="0 0 9 11"><path d="M0 0h6l3 3v8H0z" fill="#dff1fb"/></svg>Consectetuer adipiscing elit</div>
    <div class="abs blog-item" style="top:1083px"><svg width="9" height="11" viewBox="0 0 9 11"><path d="M0 0h6l3 3v8H0z" fill="#dff1fb"/></svg>Sed diam nonummy nibh.</div>
    <div class="abs blog-item" style="top:1109px"><svg width="9" height="11" viewBox="0 0 9 11"><path d="M0 0h6l3 3v8H0z" fill="#dff1fb"/></svg>Euismod tincidunt ut laoreet.</div>
    <div class="abs footer-divider" style="left:768px"></div>

    <h4 class="abs footer-heading" style="left:796px">Partners</h4>
    <div class="abs partner-badge" style="left:795px;top:1030px"></div>
    <div class="abs partner-badge" style="left:867px;top:1030px"></div>
    <div class="abs partner-badge" style="left:795px;top:1083px"></div>
    <div class="abs partner-badge" style="left:867px;top:1083px"></div>

    <div class="abs bottom-bar">All Right Reserved 2015. Maplewick Haven Supply.</div>
  </footer>
</div>
</body>
</html>
```